Accounting firm needing business card / letterhead designed
Marcus L. Trenholm, CPA
marcus@veltrowledger.com
www.veltrowledger.com
842 E Alder Ave Brennick Falls, OH 43827
555-562-0974

```html
<!DOCTYPE html>
<html lang="en">
<head>
<meta charset="utf-8">
<title>Veltro Ledger – Business Card</title>
<link rel="stylesheet" href="https://fonts.googleapis.com/css2?family=Exo+2:wght@600;700&family=Roboto:wght@400&display=swap">
<style>
  :root {
    --navy: #26215f;
    --green: #8dc63f;
    --paper: #f1f1f1;
    --white: #ffffff;
    --backdrop: #cfcfcf;
  }
  * { margin: 0; padding: 0; box-sizing: border-box; }
  html, body {
    width: 1200px;
    height: 960px;
    overflow: hidden;
    background: var(--backdrop);
  }
  .canvas {
    position: relative;
    width: 1200px;
    height: 960px;
  }
  .card {
    position: absolute;
    border-radius: 18px;
    overflow: hidden;
  }
  /* Front side */
  .card-front {
    left: 320px;
    top: 105px;
    width: 610px;
    height: 345px;
    background: var(--navy);
    color: var(--white);
  }
  .brand-name {
    position: absolute;
    left: 0;
    right: 0;
    text-align: center;
    font-family: "Exo 2", sans-serif;
    font-weight: 700;
    letter-spacing: 3px;
    white-space: nowrap;
  }
  .card-front .brand-name {
    top: 140px;
    font-size: 52px;
    line-height: 60px;
    color: var(--white);
  }
  .front-website {
    position: absolute;
    left: 0;
    right: 0;
    top: 284px;
    text-align: center;
    font-family: "Roboto", sans-serif;
    font-size: 14px;
    letter-spacing: 6px;
    color: var(--white);
    white-space: nowrap;
  }
  /* Back side */
  .card-back {
    left: 320px;
    top: 493px;
    width: 600px;
    height: 342px;
    background: var(--paper);
  }
  .name-band {
    position: absolute;
    left: 0; top: 0;
    width: 100%;
    height: 63px;
    background: var(--green);
    display: flex;
    align-items: center;
    justify-content: center;
    font-family: "Exo 2", sans-serif;
    font-weight: 700;
    font-size: 17px;
    letter-spacing: 1px;
    color: var(--white);
    white-space: nowrap;
  }
  .card-back .brand-name {
    top: 142px;
    font-size: 50px;
    line-height: 60px;
    color: var(--navy);
  }
  .contact-band {
    position: absolute;
    left: 0; bottom: 0;
    width: 100%;
    height: 75px;
    background: var(--navy);
    display: flex;
    flex-direction: column;
    justify-content: center;
    align-items: center;
    gap: 3px;
    font-family: "Roboto", sans-serif;
    font-size: 14px;
    line-height: 17px;
    color: var(--white);
    white-space: nowrap;
  }
</style>
</head>
<body>
  <main class="canvas">
    <section class="card card-front" aria-label="Business card front">
      <div class="brand-name">VELTRO LEDGER</div>
      <div class="front-website">www.veltrowledger.com</div>
    </section>

    <section class="card card-back" aria-label="Business card back">
      <div class="name-band">MARCUS L. TRENHOLM, CPA</div>
      <div class="brand-name">VELTRO LEDGER</div>
      <div class="contact-band">
        <p class="contact-address">842 E Alder Ave, Brennick Falls, OH 43827</p>
        <p class="contact-lines">C: 555-562-0974 E: marcus@veltrowledger.com W: www.veltrowledger.com</p>
      </div>
    </section>
  </main>
</body>
</html>
```